Machining Business Order Thank You Insert

I am looking for a business style card to include with orders that I ship. The card needs to thank the recipient for their order, and encourage them to leave a review. The card should include my business name and contact information and have an area to hand write a message.

I mainly sale on Craftlane and my own website. We are a machining an manufacturing business that are in the sale of mostly metal machined and 3d printed plastic products.

The front of the card should include the following:
Logo: (attached)
Snapgram: https://www.snapgram.example/kelvomill/
Friendsbook: https://www.friendsbook.example/KelvoMill
Website: https://www.kelvomill.example/

The back of the card needs an area to write a message

Industry/Entity Type

3D Printing, Machining, Craftlane

Contact Information for Business Card

Black or white front, white back to write a personal message

Font styles to use
Sans Serif

Colors

Designer to choose colors to be used in the design.

Requirements
Must have
• Encourage a review, social media info

```html
<!DOCTYPE html>
<html lang="en">
<head>
<meta charset="utf-8">
<title>KelvoMill – Thank You Card</title>
<link rel="stylesheet" href="https://fonts.googleapis.com/css2?family=Arimo:wght@400;700&display=swap">
<style>
  :root {
    --backdrop: #e8e8e6;
    --paper: #fbfbfa;
    --ink-grey: #6e6e70;
    --rule-grey: #8a8a8c;
    --write-line: #c9c9cb;
    --accent: #e8521c;
    --edge: #d2461a;
    --dark-band: #29292b;
    --light-text: #e4e4e4;
  }
  html, body {
    margin: 0;
    padding: 0;
    width: 1200px;
    height: 801px;
    overflow: hidden;
    background: var(--backdrop);
    font-family: "Arimo", Arial, sans-serif;
  }
  .canvas {
    position: relative;
    width: 1200px;
    height: 801px;
  }
  .card {
    position: absolute;
    top: 245px;
    width: 520px;
    height: 300px;
    box-sizing: border-box;
    border-bottom: 4px solid var(--edge);
    box-shadow: 0 6px 18px rgba(0,0,0,0.18);
    overflow: hidden;
    background: var(--paper);
  }

  /* Front */
  .card--front { left: 50px; }
  .brand {
    position: absolute;
    right: 36px;
    top: 44px;
    display: flex;
    align-items: center;
    gap: 12px;
  }
  .brand__square {
    width: 22px;
    height: 22px;
    background: var(--accent);
  }
  .brand__name {
    font-size: 22px;
    letter-spacing: 9px;
    text-transform: uppercase;
    color: var(--ink-grey);
  }
  .person {
    position: absolute;
    left: 36px;
    top: 112px;
  }
  .person__name {
    font-size: 21px;
    font-weight: 700;
    color: var(--accent);
    line-height: 1;
  }
  .person__role {
    font-size: 15px;
    color: var(--ink-grey);
    margin-top: 5px;
  }
  .divider {
    position: absolute;
    left: 36px;
    right: 36px;
    top: 162px;
    height: 1px;
    background: var(--rule-grey);
  }
  .contacts {
    position: absolute;
    left: 36px;
    top: 178px;
    margin: 0;
    padding: 0;
    list-style: none;
  }
  .contacts li {
    display: flex;
    align-items: center;
    gap: 10px;
    font-size: 15px;
    color: var(--ink-grey);
    line-height: 26px;
  }
  .contacts__dot {
    width: 13px;
    height: 13px;
    border-radius: 50%;
    background: var(--accent);
    flex: none;
  }
  .address {
    position: absolute;
    right: 36px;
    top: 182px;
    text-align: right;
    font-size: 15px;
    color: var(--ink-grey);
    line-height: 20px;
  }

  /* Back */
  .card--back { left: 630px; }
  .thanks {
    position: absolute;
    left: 36px;
    top: 30px;
    margin: 0;
    font-size: 21px;
    font-weight: 700;
    color: var(--accent);
    line-height: 1;
  }
  .review-prompt {
    position: absolute;
    left: 36px;
    right: 36px;
    top: 60px;
    margin: 0;
    font-size: 14px;
    color: var(--ink-grey);
    line-height: 19px;
  }
  .message-area {
    position: absolute;
    left: 36px;
    right: 36px;
    top: 112px;
  }
  .message-area__line {
    height: 32px;
    border-bottom: 1px solid var(--write-line);
  }
  .back-band {
    position: absolute;
    left: 0;
    right: 0;
    bottom: 0;
    height: 48px;
    background: var(--dark-band);
    display: flex;
    align-items: center;
    justify-content: flex-end;
    padding-right: 36px;
  }
  .back-band__name {
    font-size: 17px;
    letter-spacing: 8px;
    text-transform: uppercase;
    color: var(--light-text);
  }
</style>
</head>
<body>
<main class="canvas">
  <section class="card card--front" aria-label="Card front">
    <div class="brand">
      <span class="brand__square" aria-hidden="true"></span>
      <span class="brand__name">KelvoMill</span>
    </div>
    <div class="person">
      <div class="person__name">Marcus Ellery</div>
      <div class="person__role">Manager</div>
    </div>
    <div class="divider" aria-hidden="true"></div>
    <ul class="contacts">
      <li><span class="contacts__dot" aria-hidden="true"></span>kelvomill</li>
      <li><span class="contacts__dot" aria-hidden="true"></span>KelvoMill</li>
      <li><span class="contacts__dot" aria-hidden="true"></span>www.kelvomill.example</li>
    </ul>
    <div class="address">Your address, city<br>state, ZIP 0000</div>
  </section>

  <section class="card card--back" aria-label="Card back">
    <h2 class="thanks">Thank you for your order!</h2>
    <p class="review-prompt">We'd love your feedback – please leave us a review on Craftlane or at www.kelvomill.example</p>
    <div class="message-area" aria-label="Space for a handwritten message">
      <div class="message-area__line"></div>
      <div class="message-area__line"></div>
      <div class="message-area__line"></div>
    </div>
    <div class="back-band">
      <span class="back-band__name">KelvoMill</span>
    </div>
  </section>
</main>
</body>
</html>
```